jQuery Mobile CSS for web app

Task Outline:
Create jQuery Mobile themeroller compliant CSS and icons for a mobile web app.
Task Description:
Brindle Solutions are in the process of implementing a new, web based version of their Tessel operations platform.
The web based version of Tessel is built on top of the jQuery Mobile platform and we are looking for a designer to create a jQuery Mobile themeroller compliant CSS theme pack that we can plug into our application. The aim is to remove the standard jQuery Mobile look and feel and to introduce the Brindle branding throughout the new web app.
A number of screenshots are shown in the attached design spec (brindle_solutions.pdf) that show what the current (Windows Mobile 6.5) application looks like, alongside the development version of our new web app.
Deliverables:
• jQuery Mobile (v 1.4.2) themeroller compliant CSS which provides theming for all jQuery Mobile UI components.
• Example html showing how to use the CSS theme (especially where additional html/css classes are required).
• New set of status icons (as listed in attachment)
Inspiration:
See our website for current branding: www.brindle-solutions-demo.net

```html
<!DOCTYPE html>
<html lang="en">
<head>
<meta charset="utf-8">
<title>Brindle Tessel – Home</title>
<link href="https://fonts.googleapis.com/css2?family=Roboto:wght@400;500&display=swap" rel="stylesheet">
<style>
  :root {
    --header-top: #4a4a4c;
    --header-bottom: #232325;
    --body-bg: #3b3a3f;
    --footer-bg: #1e1e1f;
    --text: #ffffff;
    --menu-bar: #b9b9bb;
    --tile-blue: #2e93dc;
    --tile-blue-dark: #1b6fb5;
    --tile-red: #ee4631;
    --tile-red-dark: #c42a1a;
    --tile-purple: #9533d6;
    --tile-purple-dark: #6c1fae;
    --tile-royal: #1f33ea;
    --tile-royal-dark: #0f1cb8;
    --tile-olive: #cfc800;
    --tile-olive-dark: #a49d00;
    --icon-light: #ffffff;
  }
  * { box-sizing: border-box; margin: 0; padding: 0; }
  html, body { width: 956px; height: 1200px; overflow: hidden; }
  body {
    background: var(--body-bg);
    font-family: "Roboto", Arial, sans-serif;
    color: var(--text);
    position: relative;
  }
  .app-header {
    position: absolute; left: 0; top: 0; width: 956px; height: 141px;
    background: linear-gradient(var(--header-top), var(--header-bottom));
    border-bottom: 2px solid #111;
  }
  .app-title {
    position: absolute; left: 90px; top: 42px;
    font-size: 45px; font-weight: 400; letter-spacing: 0.5px;
  }
  .menu-button { position: absolute; right: 38px; top: 28px; width: 76px; height: 80px; }
  .menu-button span {
    display: block; height: 18px; margin-bottom: 8px; border-radius: 3px;
    background: linear-gradient(#d4d4d6, #8e8e90);
  }
  .launcher { position: absolute; left: 0; top: 141px; width: 956px; height: 940px; }
  .tile { position: absolute; width: 200px; text-align: center; }
  .tile-face {
    width: 163px; height: 152px; margin: 0 auto; border-radius: 10px;
    position: relative; overflow: hidden;
    box-shadow: 0 6px 8px rgba(0,0,0,0.55);
  }
  .tile-face::after {
    content: ""; position: absolute; left: 0; top: 0; right: 0; height: 48%;
    background: linear-gradient(rgba(255,255,255,0.28), rgba(255,255,255,0.06));
  }
  .tile-face svg { position: absolute; left: 0; top: 0; width: 163px; height: 152px; z-index: 1; }
  .tile-label { display: block; margin-top: 18px; font-size: 31px; }
  .tile-blue   { background: linear-gradient(var(--tile-blue), var(--tile-blue-dark)); }
  .tile-red    { background: linear-gradient(var(--tile-red), var(--tile-red-dark)); }
  .tile-purple { background: linear-gradient(var(--tile-purple), var(--tile-purple-dark)); }
  .tile-royal  { background: linear-gradient(var(--tile-royal), var(--tile-royal-dark)); }
  .tile-olive  { background: linear-gradient(var(--tile-olive), var(--tile-olive-dark)); }
  .col-1 { left: 82px; } .col-2 { left: 362px; } .col-3 { left: 642px; }
  .row-1 { top: 82px; } .row-2 { top: 364px; } .row-3 { top: 644px; }
  .app-footer {
    position: absolute; left: 0; top: 1081px; width: 956px; height: 119px;
    background: var(--footer-bg);
  }
  .device-code { position: absolute; right: 30px; top: 60px; font-size: 32px; }
</style>
</head>
<body>
  <header class="app-header">
    <h1 class="app-title">Brindle Tessel</h1>
    <div class="menu-button" aria-label="Menu"><span></span><span></span><span></span></div>
  </header>

  <main class="launcher">
    <div class="tile col-1 row-1">
      <div class="tile-face tile-blue">
        <svg viewBox="0 0 60 56"><circle cx="30" cy="20" r="7" fill="#fff"/><path d="M17 42c0-9 5-13 13-13s13 4 13 13z" fill="#fff"/><path d="M28 30l2 6 2-6z" fill="#2a85cf"/></svg>
      </div>
      <span class="tile-label">My Work</span>
    </div>
    <div class="tile col-2 row-1">
      <div class="tile-face tile-red">
        <svg viewBox="0 0 60 56"><g fill="#fff"><path d="M19 15l4-2 22 23-4 4-22-23z"/><path d="M41 13a6 6 0 0 0-7 8L18 37l3 3 16-16a6 6 0 0 0 8-7l-4 3-3-1-1-3z"/></g></svg>
      </div>
      <span class="tile-label">New Job Order</span>
    </div>
    <div class="tile col-3 row-1">
      <div class="tile-face tile-red">
        <svg viewBox="0 0 60 56"><g fill="#fff"><path d="M19 15l4-2 22 23-4 4-22-23z"/><path d="M41 13a6 6 0 0 0-7 8L18 37l3 3 16-16a6 6 0 0 0 8-7l-4 3-3-1-1-3z"/></g></svg>
      </div>
      <span class="tile-label">Filed</span>
    </div>

    <div class="tile col-1 row-2">
      <div class="tile-face tile-purple">
        <svg viewBox="0 0 60 56"><circle cx="33" cy="23" r="8" fill="none" stroke="#fff" stroke-width="3.5"/><path d="M27 29l-9 9" stroke="#fff" stroke-width="5" stroke-linecap="round"/></svg>
      </div>
      <span class="tile-label">Timessheet</span>
    </div>
    <div class="tile col-2 row-2">
      <div class="tile-face tile-royal">
        <svg viewBox="0 0 60 56"><path d="M30 12l4 3 5-1 1 5 4 3-2 5 2 5-4 3-1 5-5-1-4 3-4-3-5 1-1-5-4-3 2-5-2-5 4-3 1-5 5 1z" fill="#fff"/><path d="M24 28l4 4 8-9" fill="none" stroke="#1a2bd8" stroke-width="3.5" stroke-linecap="round" stroke-linejoin="round"/></svg>
      </div>
      <span class="tile-label">Authorisation</span>
    </div>
    <div class="tile col-3 row-2">
      <div class="tile-face tile-olive">
        <svg viewBox="0 0 60 56"><path d="M30 12l14 7-14 7-14-7z" fill="#fff"/><path d="M16 21l13 7v16l-13-7z" fill="#f1f0d0"/><path d="M44 21l-13 7v16l13-7z" fill="#dedcb0"/></svg>
      </div>
      <span class="tile-label">Asset</span>
    </div>

    <div class="tile col-1 row-3">
      <div class="tile-face tile-olive">
        <svg viewBox="0 0 60 56"><path d="M26 19l12 6-12 6-12-6z" fill="#fff"/><path d="M14 27l11 6v13l-11-6z" fill="#f1f0d0"/><path d="M38 27l-11 6v13l11-6z" fill="#dedcb0"/><g fill="none" stroke="#fff" stroke-width="2" stroke-linecap="round"><path d="M38 17a4 4 0 0 1 4 4"/><path d="M38 12a9 9 0 0 1 9 9"/><path d="M38 7a14 14 0 0 1 14 14"/></g></svg>
      </div>
      <span class="tile-label">Tag it</span>
    </div>
    <div class="tile col-2 row-3">
      <div class="tile-face tile-red">
        <svg viewBox="0 0 60 56"><g fill="#fff"><path d="M19 15l4-2 22 23-4 4-22-23z"/><path d="M41 13a6 6 0 0 0-7 8L18 37l3 3 16-16a6 6 0 0 0 8-7l-4 3-3-1-1-3z"/></g></svg>
      </div>
      <span class="tile-label">Form Test</span>
    </div>
  </main>

  <footer class="app-footer">
    <span class="device-code">C6</span>
  </footer>
</body>
</html>
```